We are looking to create a graphic that will be used in Facebook posts each week to show the daily Mosquito Forecast. Attached is an example of what we are looking for. We need to be able to update the forecast. So we will need hi-res vector files. The graphics need to represent the level of mosquito activity: SLIGHT, AVERAGE, INTENSE, EXTREME

```html
<!DOCTYPE html>
<html lang="en">
<head>
<meta charset="utf-8">
<title>Mosquito Forecast – Weekly Graphic</title>
<link rel="stylesheet" href="https://fonts.googleapis.com/css2?family=Fira+Sans:wght@700&family=Poppins:wght@400;500;600&family=Open+Sans:wght@600&family=Righteous&display=swap">
<style>
  :root {
    --page-bg: #d3d5d7;
    --band-bg: #dfe1e2;
    --title-ink: #1f2a0e;
    --subtitle-ink: #0f4d2a;
    --field-dark: #1d3a17;
    --field-mid: #3f6b2c;
    --field-light: #6f9550;
    --headline: #f3ee1c;
    --headline-shadow: #2a2a00;
    --panel: #ffffff;
    --ink: #1a1a1a;
    --muted: #555555;
    --rule: #bdbdbd;
    --off: #e6e6e6;
    --slight: #5cb946;
    --average: #ffb700;
    --intense: #ff6640;
    --extreme: #d9000d;
  }
  * { margin: 0; padding: 0; box-sizing: border-box; }
  html, body { width: 1200px; height: 781px; overflow: hidden; }
  body {
    position: relative;
    background: linear-gradient(180deg, #d0d2d4 0%, #dcdedf 100%);
    font-family: "Poppins", sans-serif;
    color: var(--ink);
  }
  .sheet-title {
    position: absolute; left: 0; top: 46px; width: 1200px;
    text-align: center;
    font-family: "Fira Sans", sans-serif; font-weight: 700;
    font-size: 58px; line-height: 1; color: var(--title-ink);
  }
  .sheet-band {
    position: absolute; left: 0; top: 134px; width: 1200px; height: 58px;
    background: var(--band-bg);
    display: flex; align-items: center; justify-content: center;
    font-family: "Poppins", sans-serif; font-weight: 500;
    font-size: 27px; color: var(--subtitle-ink); letter-spacing: 0.5px;
  }
  .post {
    position: absolute; left: 78px; top: 210px; width: 1044px; height: 548px;
    overflow: hidden;
  }
  .post-photo {
    position: absolute; inset: 0;
    background:
      radial-gradient(ellipse at 30% 25%, rgba(140,170,100,.45), transparent 55%),
      radial-gradient(ellipse at 80% 40%, rgba(120,150,90,.35), transparent 50%),
      linear-gradient(180deg, var(--field-light) 0%, var(--field-mid) 45%, var(--field-dark) 100%);
  }
  .post-headline {
    position: absolute; left: 0; top: 98px; width: 1044px; text-align: center;
    font-family: "Righteous", sans-serif; font-size: 72px; line-height: 1;
    letter-spacing: 1px;
    color: var(--headline-shadow);
    -webkit-text-stroke: 2.5px var(--headline);
    text-shadow: 0 0 4px rgba(0,0,0,.5);
  }
  .post-location {
    position: absolute; left: 0; top: 160px; width: 1044px; text-align: center;
    font-family: "Open Sans", sans-serif; font-weight: 600;
    font-size: 43px; line-height: 1.1; color: #ffffff;
    text-shadow: 0 2px 3px rgba(0,0,0,.55);
  }
  .forecast {
    position: absolute; left: 18px; top: 240px; width: 1007px; height: 262px;
    background: var(--panel);
  }
  .days {
    position: absolute; left: 9px; top: 28px;
    display: grid; grid-template-columns: repeat(7, 141.2px);
  }
  .day {
    height: 183px; text-align: center; position: relative;
  }
  .day + .day { border-left: 1px solid var(--rule); }
  .day-name { font-size: 16px; font-weight: 400; line-height: 1; padding-top: 10px; }
  .day-date { font-size: 10.5px; color: var(--muted); margin-top: 6px; line-height: 1; }
  .gauge { display: block; margin: 17px auto 0; }
  .day-level { font-size: 12px; font-weight: 600; margin-top: 0; letter-spacing: .3px; }
  .baseline {
    position: absolute; left: 34px; top: 211px; width: 952px; height: 1px;
    background: var(--rule);
  }
  .legend {
    position: absolute; left: 0; top: 229px; width: 1007px;
    display: flex; justify-content: center; align-items: center; gap: 10px;
    font-size: 9.5px; font-weight: 500;
  }
  .legend-item { display: flex; align-items: center; gap: 5px; margin-right: 4px; }
  .swatch { width: 18px; height: 18px; }
  .seg { fill: none; stroke-width: 13; stroke-dasharray: 25.2 300; }
  .seg.off { stroke: var(--off); }
  .seg.g { stroke: var(--slight); }
  .seg.y { stroke: var(--average); }
  .seg.o { stroke: var(--intense); }
  .seg.r { stroke: var(--extreme); }
  .frame { fill: none; stroke: #111; stroke-width: 1.3; }
  .hub { fill: #fff; stroke: #111; stroke-width: 5; }
  .lvl-slight { fill: var(--slight); }
  .lvl-average { fill: var(--average); }
  .lvl-intense { fill: var(--intense); }
  .lvl-extreme { fill: var(--extreme); }
  .icon-spot { opacity: .3; }
</style>
</head>
<body>
  <h1 class="sheet-title">Mosquito Forecast</h1>
  <div class="sheet-band">Revision 3 - Mockup 3c</div>

  <section class="post">
    <div class="post-photo" role="img" aria-label="Close-up photo of a green wheat field"></div>
    <h2 class="post-headline">MOSCUITO FORECAST</h2>
    <p class="post-location">Greater Milwakukee</p>

    <div class="forecast">
      <div class="days">
        <!-- Mon -->
        <div class="day">
          <div class="day-name">Mon</div><div class="day-date">02/20</div>
          <svg class="gauge" width="112" height="104" viewBox="-60 -58 120 112">
            <path class="frame" d="M-38.2 38.2 A54 54 0 1 1 38.2 38.2 L21.2 21.2 M-38.2 38.2 L-21.2 21.2"/>
            <circle class="seg g" r="46" transform="rotate(136)"/><circle class="seg g" r="46" transform="rotate(169.75)"/>
            <circle class="seg off" r="46" transform="rotate(203.5)"/><circle class="seg off" r="46" transform="rotate(237.25)"/>
            <circle class="seg off" r="46" transform="rotate(271)"/><circle class="seg off" r="46" transform="rotate(304.75)"/>
            <circle class="seg off" r="46" transform="rotate(338.5)"/><circle class="seg off" r="46" transform="rotate(372.25)"/>
            <circle class="hub" r="28"/>
            <circle class="icon-spot lvl-slight" r="20" role="img" aria-label="Mosquito icon, green"/>
          </svg>
          <div class="day-level">Slight</div>
        </div>
        <!-- Tue -->
        <div class="day">
          <div class="day-name">Tue</div><div class="day-date">02/21</div>
          <svg class="gauge" width="112" height="104" viewBox="-60 -58 120 112">
            <path class="frame" d="M-38.2 38.2 A54 54 0 1 1 38.2 38.2 L21.2 21.2 M-38.2 38.2 L-21.2 21.2"/>
            <circle class="seg g" r="46" transform="rotate(136)"/><circle class="seg g" r="46" transform="rotate(169.75)"/>
            <circle class="seg y" r="46" transform="rotate(203.5)"/><circle class="seg y" r="46" transform="rotate(237.25)"/>
            <circle class="seg off" r="46" transform="rotate(271)"/><circle class="seg off" r="46" transform="rotate(304.75)"/>
            <circle class="seg off" r="46" transform="rotate(338.5)"/><circle class="seg off" r="46" transform="rotate(372.25)"/>
            <circle class="hub" r="28"/>
            <circle class="icon-spot lvl-average" r="20" role="img" aria-label="Mosquito icon, yellow"/>
          </svg>
          <div class="day-level">Average</div>
        </div>
        <!-- Wed -->
        <div class="day">
          <div class="day-name">Wed</div><div class="day-date">02/22</div>
          <svg class="gauge" width="112" height="104" viewBox="-60 -58 120 112">
            <path class="frame" d="M-38.2 38.2 A54 54 0 1 1 38.2 38.2 L21.2 21.2 M-38.2 38.2 L-21.2 21.2"/>
            <circle class="seg g" r="46" transform="rotate(136)"/><circle class="seg g" r="46" transform="rotate(169.75)"/>
            <circle class="seg y" r="46" transform="rotate(203.5)"/><circle class="seg y" r="46" transform="rotate(237.25)"/>
            <circle class="seg o" r="46" transform="rotate(271)"/><circle class="seg o" r="46" transform="rotate(304.75)"/>
            <circle class="seg off" r="46" transform="rotate(338.5)"/><circle class="seg off" r="46" transform="rotate(372.25)"/>
            <circle class="hub" r="28"/>
            <circle class="icon-spot lvl-intense" r="20" role="img" aria-label="Mosquito icon, orange"/>
          </svg>
          <div class="day-level">Intense</div>
        </div>
        <!-- Thu -->
        <div class="day">
          <div class="day-name">Thu</div><div class="day-date">02/23</div>
          <svg class="gauge" width="112" height="104" viewBox="-60 -58 120 112">
            <path class="frame" d="M-38.2 38.2 A54 54 0 1 1 38.2 38.2 L21.2 21.2 M-38.2 38.2 L-21.2 21.2"/>
            <circle class="seg g" r="46" transform="rotate(136)"/><circle class="seg g" r="46" transform="rotate(169.75)"/>
            <circle class="seg y" r="46" transform="rotate(203.5)"/><circle class="seg y" r="46" transform="rotate(237.25)"/>
            <circle class="seg o" r="46" transform="rotate(271)"/><circle class="seg o" r="46" transform="rotate(304.75)"/>
            <circle class="seg r" r="46" transform="rotate(338.5)"/><circle class="seg r" r="46" transform="rotate(372.25)"/>
            <circle class="hub" r="28"/>
            <circle class="icon-spot lvl-extreme" r="20" role="img" aria-label="Mosquito icon, red"/>
          </svg>
          <div class="day-level">Extreme</div>
        </div>
        <!-- Fri -->
        <div class="day">
          <div class="day-name">Fri</div><div class="day-date">02/24</div>
          <svg class="gauge" width="112" height="104" viewBox="-60 -58 120 112">
            <path class="frame" d="M-38.2 38.2 A54 54 0 1 1 38.2 38.2 L21.2 21.2 M-38.2 38.2 L-21.2 21.2"/>
            <circle class="seg g" r="46" transform="rotate(136)"/><circle class="seg g" r="46" transform="rotate(169.75)"/>
            <circle class="seg y" r="46" transform="rotate(203.5)"/><circle class="seg y" r="46" transform="rotate(237.25)"/>
            <circle class="seg off" r="46" transform="rotate(271)"/><circle class="seg off" r="46" transform="rotate(304.75)"/>
            <circle class="seg off" r="46" transform="rotate(338.5)"/><circle class="seg off" r="46" transform="rotate(372.25)"/>
            <circle class="hub" r="28"/>
            <circle class="icon-spot lvl-average" r="20" role="img" aria-label="Mosquito icon, yellow"/>
          </svg>
          <div class="day-level">Average</div>
        </div>
        <!-- Sat -->
        <div class="day">
          <div class="day-name">Sat</div><div class="day-date">02/25</div>
          <svg class="gauge" width="112" height="104" viewBox="-60 -58 120 112">
            <path class="frame" d="M-38.2 38.2 A54 54 0 1 1 38.2 38.2 L21.2 21.2 M-38.2 38.2 L-21.2 21.2"/>
            <circle class="seg g" r="46" transform="rotate(136)"/><circle class="seg g" r="46" transform="rotate(169.75)"/>
            <circle class="seg y" r="46" transform="rotate(203.5)"/><circle class="seg y" r="46" transform="rotate(237.25)"/>
            <circle class="seg o" r="46" transform="rotate(271)"/><circle class="seg o" r="46" transform="rotate(304.75)"/>
            <circle class="seg off" r="46" transform="rotate(338.5)"/><circle class="seg off" r="46" transform="rotate(372.25)"/>
            <circle class="hub" r="28"/>
            <circle class="icon-spot lvl-intense" r="20" role="img" aria-label="Mosquito icon, orange"/>
          </svg>
          <div class="day-level">Intense</div>
        </div>
        <!-- Sun -->
        <div class="day">
          <div class="day-name">Sun</div><div class="day-date">02/26</div>
          <svg class="gauge" width="112" height="104" viewBox="-60 -58 120 112">
            <path class="frame" d="M-38.2 38.2 A54 54 0 1 1 38.2 38.2 L21.2 21.2 M-38.2 38.2 L-21.2 21.2"/>
            <circle class="seg g" r="46" transform="rotate(136)"/><circle class="seg g" r="46" transform="rotate(169.75)"/>
            <circle class="seg y" r="46" transform="rotate(203.5)"/><circle class="seg y" r="46" transform="rotate(237.25)"/>
            <circle class="seg o" r="46" transform="rotate(271)"/><circle class="seg o" r="46" transform="rotate(304.75)"/>
            <circle class="seg r" r="46" transform="rotate(338.5)"/><circle class="seg r" r="46" transform="rotate(372.25)"/>
            <circle class="hub" r="28"/>
            <circle class="icon-spot lvl-extreme" r="20" role="img" aria-label="Mosquito icon, red"/>
          </svg>
          <div class="day-level">Extreme</div>
        </div>
      </div>

      <div class="baseline"></div>

      <div class="legend">
        <div class="legend-item"><span class="swatch" style="background:var(--slight)"></span>Slight</div>
        <div class="legend-item"><span class="swatch" style="background:var(--average)"></span>Average</div>
        <div class="legend-item"><span class="swatch" style="background:var(--intense)"></span>Intense</div>
        <div class="legend-item"><span class="swatch" style="background:var(--extreme)"></span>Extreme</div>
      </div>
    </div>
  </section>
</body>
</html>
```